KRV Business Card

Looking for a business card for my restaurant group I own. Four different concepts:

Copperfield Alehouse
Bristow Alehouse
Tanager's Stone Hearth Kitchen
Pellston Patty Company

Card doesn't need to include all the logos.

```html
<!DOCTYPE html>
<html lang="en">
<head>
<meta charset="utf-8">
<title>KRV Business Card</title>
<link rel="stylesheet" href="https://fonts.googleapis.com/css2?family=Lato:wght@700;900&family=Open+Sans:wght@400;600&display=swap">
<style>
  :root {
    --backdrop: #8c5227;
    --card-light: #d8b486;
    --card-mid: #c49a68;
    --card-dark: #b0834f;
    --ink: #141010;
    --rule: #6e5538;
  }
  * { margin: 0; padding: 0; box-sizing: border-box; }
  html, body { width: 1200px; height: 900px; overflow: hidden; }
  body { background: var(--backdrop); position: relative; color: var(--ink); }

  .card {
    position: absolute;
    background: linear-gradient(160deg, var(--card-light) 0%, var(--card-mid) 55%, var(--card-dark) 100%);
    text-align: center;
  }
  .card--contact { left: 330px; top: 90px; width: 555px; height: 343px; font-family: "Open Sans", sans-serif; }
  .card--brand { left: 330px; top: 469px; width: 558px; height: 343px; font-family: "Lato", sans-serif; }

  .row { position: absolute; left: 0; width: 100%; }

  .holder-name { top: 64px; font-size: 20px; font-weight: 600; letter-spacing: 0.2px; }
  .holder-title { top: 87px; font-size: 16px; }
  .rule { position: absolute; height: 1px; background: var(--rule); }
  .card--contact .rule { width: 195px; left: 180px; }
  .rule--upper { top: 117px; }
  .rule--lower { top: 222px; }
  .contact-list { top: 128px; font-size: 16px; line-height: 20.3px; list-style: none; }
  .contact-list b { font-weight: 600; }
  .address { top: 239px; font-size: 16px; line-height: 20px; }

  .brand-initials { top: 80px; font-size: 74px; font-weight: 900; letter-spacing: 2px; line-height: 1; }
  .brand-name { top: 170px; font-size: 40px; font-weight: 900; letter-spacing: 7px; line-height: 1; }
  .brand-tagline { top: 220px; font-size: 20px; font-weight: 900; letter-spacing: 2.5px; line-height: 1; }
  .card--brand .rule { width: 310px; left: 123px; top: 263px; background: var(--ink); }
  .venues { top: 272px; font-size: 14.5px; font-weight: 900; line-height: 18px; letter-spacing: 0.2px; }
</style>
</head>
<body>
  <section class="card card--contact">
    <p class="row holder-name">DANIEL HARPER</p>
    <p class="row holder-title">Managing Director</p>
    <div class="rule rule--upper"></div>
    <ul class="row contact-list">
      <li><b>P:</b> 044-555 010 234</li>
      <li><b>M:</b> 044-555 010 234</li>
      <li><b>E:</b> info@kestrelhg.com</li>
      <li><b>W:</b> www.kestrelhg.com</li>
    </ul>
    <div class="rule rule--lower"></div>
    <p class="row address">12345, Address Goes Here<br>Country Name, 123456.</p>
  </section>

  <section class="card card--brand">
    <p class="row brand-initials">KRV</p>
    <p class="row brand-name">KESTREL</p>
    <p class="row brand-tagline">HOSPITALITY GROUP</p>
    <div class="rule"></div>
    <p class="row venues">COPPERFIELD ALEHOUSE &nbsp;|&nbsp; BRISTOW ALEHOUSE<br>TANAGER'S STONE HEARTH KITCHEN &nbsp;|&nbsp; PELLSTON PATTY COMPANY</p>
  </section>
</body>
</html>
```